Recruitment Agency in Texas, needs a stand out header letter

Our colours are red and grey and can be found on our website
just my logo will be sufficient and address...

Target Market(s)

Engineering Manufacturing

Colors
0094D4
00A9DD
6FCCEA
C7EBF8
E9F6FB
EB3D1F
EC4F4E
F09395
F8D3D4
FCEDEE

Requirements
Must have
• use colors red and grey
Should not have
• Please use same colors and font as my logo. My website is keltrayrecruitment.com

```html
<!DOCTYPE html>
<html lang="en">
<head>
<meta charset="utf-8">
<title>KeltrayRecruitment Letterhead</title>
<link rel="stylesheet" href="https://fonts.googleapis.com/css2?family=Heebo:wght@300;400;700&family=Ubuntu:wght@500&family=Pinyon+Script&display=swap">
<style>
  :root {
    --brand-red: #dd1f26;
    --brand-grey: #58595b;
    --ink: #2b2b2b;
    --paper: #f4f4f4;
    --backdrop: #e4e4e4;
  }
  * { margin: 0; padding: 0; box-sizing: border-box; }
  html, body {
    width: 1200px; height: 1200px; overflow: hidden;
    background: var(--backdrop);
  }
  .letterhead {
    position: absolute;
    left: 211px; top: 50px;
    width: 778px; height: 1100px;
    background: var(--paper);
    box-shadow: 0 2px 10px rgba(0,0,0,0.12);
    font-family: "Heebo", "Helvetica Neue", Arial, sans-serif;
    font-weight: 300;
    color: var(--ink);
  }
  .brand-name {
    position: absolute;
    top: 36px; left: 0; right: 0;
    text-align: center;
    font-family: "Ubuntu", "Heebo", sans-serif;
    font-weight: 500;
    font-size: 33px;
    letter-spacing: -0.5px;
    color: var(--brand-red);
  }
  .letter-body {
    position: absolute;
    left: 83px; top: 257px;
    width: 611px;
    font-size: 13px;
    line-height: 18.3px;
  }
  .letter-date { margin-bottom: 18px; }
  .recipient { margin-bottom: 36px; }
  .salutation { margin-bottom: 18px; }
  .paragraph { text-align: justify; margin-bottom: 18px; }
  .closing { margin-top: 54px; }
  .signature {
    font-family: "Pinyon Script", cursive;
    font-size: 26px;
    line-height: 1.3;
    margin-left: 4px;
    color: #111;
  }
  .footer-band {
    position: absolute;
    left: 0; right: 0; bottom: 0;
    height: 33px;
    background: var(--brand-red);
    color: #fff;
    font-size: 13px;
    font-weight: 300;
    display: flex; align-items: center; justify-content: center;
  }
  .footer-band strong { font-weight: 700; margin-right: 4px; }
</style>
</head>
<body>
  <article class="letterhead">
    <header class="brand-name">KeltrayRecruitment</header>

    <section class="letter-body">
      <p class="letter-date">01 January 2050</p>
      <p class="recipient">Company (Pvt) Ltd.<br>PO Box 3355 Mainville St<br>Sample City Country 3355</p>
      <p class="salutation">Dear Daniel Hartwell,</p>
      <p class="paragraph">Lorem ipsum dolor sit amet, consectetuer adipiscing elit, sed diam nonummy nibh euismod tincidunt ut laoreet dolore magna aliquam erat volutpat. Ut wisi enim ad minim veniam, quis nostrud exerci tation ullamcorper suscipit lobortis nisl ut aliquip ex ea commodo consequat. Duis dolore te feugait nulla facilisi. Nam liber tempor cum soluta nobis eleifend option congue nihil imperdiet doming id quod mazim placerat facer possim assum. Lorem ipsum dolor sit amet, consectetuer adipiscing elit, sed diam nonummy nibh euismod tincidunt ut laoreet dolore magna aliquam erat volutpat. Ut wisi enim ad minim veniam, quis nostrud exerci tation ullamcorper suscipit lobortis nisl ut aliquip ex ea commodo consequat.</p>
      <p class="paragraph">Consectetuer adipiscing elit, sed diam nonummy nibh euismod tincidunt ut laoreet dolore magna aliquam erat volutpat. Ut wisi enim ad minim veniam, quis nostrud exerci tation ullamcorper suscipit lobortis nisl ut aliquip ex ea commodo consequat. Consectetuer adipiscing elit, sed diam nonummy nibh euismod tincidunt ut laoreet dolore magna aliquam erat volutpat. Ut wisi enim ad minim veniam, quis nostrud exerci tation ullamcorper suscipit lobortis nisl ut aliquip ex ea commodo consequat.</p>
      <p class="paragraph">Consectetuer adipiscing elit, sed diam nonummy nibh euismod tincidunt ut laoreet dolore magna aliquam erat volutpat. Ut wisi enim ad minim veniam, quis nostrud exerci tation ullamcorper suscipit lobortis nisl ut aliquip ex ea commodo consequat. Consectetuer adipiscing elit, sed diam nonummy nibh euismod tincidunt ut laoreet dolore magna aliquam erat volutpat. Ut wisi enim ad minim veniam, quis nostrud exerci tation ullamcorper suscipit lobortis nisl ut aliquip ex ea commodo consequat.</p>
      <p class="closing">Sincerely Yours</p>
      <p class="signature">Owen Calloway</p>
    </section>

    <footer class="footer-band">
      <strong>KeltrayRecruitment,</strong> Central Houston Office, 48 Ridgeline Plaza Suite 900, Houston, TX 77052
    </footer>
  </article>
</body>
</html>
```